Risk Management Company in need of Business Card Design

We sell risk management insurance to Lenders (Banks, Credit Unions, Real Estate Trust).

We need a very clean, professional card that will leave a great impression.

We are looking to use a blue color for our logo on the card (Preferably close to royal blue but are open to looking at navy blue or any darker blues as well).

Please see the logo attached to get an idea. We are open to writing Harbor Ledger Under the logo or next to the logo. Really whatever looks best.

Target Market(s)

Banks, Credit Unions, Real Estate Trusts

Industry/Entity Type

Insurance

Contact Information for Business Card

Name: Tom Brandish
Title: Regional Sales Director
Email: tbrandish@harborledger-example.net
C:410-555-0137
D:410-555-0182
888-555-0149 Ext.318
F:443-555-0164 (We would like to see some cards without the fax number as well to compare)

Company Name: Harbor Ledger
Website: www.harborledger-example.net

Address: 718 E. Marlow St. Suite 340, Towson, MD 21287 (Preferably written on the bottom of the card in small print.)

Colors
0355a3
0455a3

Requirements
Nice to have
• We would like to see a couple of where the back has the logo in reverse colors (Logo White, Background Blue)

```html
<!DOCTYPE html>
<html lang="en">
<head>
<meta charset="utf-8">
<title>Harbor Ledger – Business Card</title>
<link rel="stylesheet" href="https://fonts.googleapis.com/css2?family=Cinzel:wght@600&family=Open+Sans:wght@400;700&display=swap">
<style>
  :root {
    --backdrop: #e9e6e1;
    --card-white: #ffffff;
    --brand-blue: #0355a3;
    --brand-slate: #2f4c5a;
    --ink: #2b2b2b;
    --rule-grey: #8a8a8a;
    --faint-mark: #ececec;
  }
  * { box-sizing: border-box; margin: 0; padding: 0; }
  html, body { width: 1200px; height: 501px; overflow: hidden; }
  body { background: var(--backdrop); position: relative; font-family: "Open Sans", Arial, sans-serif; color: var(--ink); }

  .card {
    position: absolute;
    top: 88px;
    width: 530px;
    height: 325px;
    border-radius: 28px;
    overflow: hidden;
    box-shadow: 0 6px 18px rgba(0,0,0,0.18);
  }
  .card--front { left: 40px; background: var(--card-white); }
  .card--back { left: 630px; background: var(--brand-blue); color: var(--card-white); text-align: center; }

  /* front */
  .faint-mark {
    position: absolute; left: 345px; top: 95px;
    width: 150px; height: 150px; border-radius: 50%;
    background: var(--faint-mark);
  }
  .holder { position: absolute; right: 38px; top: 30px; text-align: right; }
  .holder__name { font-weight: 700; font-size: 19px; }
  .holder__title { font-size: 15px; margin-top: 2px; }
  .holder-rule { position: absolute; right: 34px; top: 84px; width: 230px; height: 2px; background: var(--rule-grey); }

  .brand-front { position: absolute; left: 34px; top: 112px; display: flex; align-items: center; gap: 10px; }
  .brand-front__dot { width: 22px; height: 22px; border-radius: 50%; background: var(--brand-slate); }
  .brand-front__name { font-family: "Cinzel", Georgia, serif; font-weight: 600; font-size: 20px; color: var(--brand-slate); letter-spacing: 0.5px; }

  .contacts { position: absolute; left: 38px; top: 176px; font-size: 13.5px; line-height: 21px; }
  .contacts__row { display: flex; align-items: center; gap: 7px; white-space: nowrap; }
  .contacts__row svg { width: 12px; height: 12px; flex: none; fill: var(--ink); }
  .contacts__pair { display: flex; gap: 22px; }
  .contacts__ext { font-size: 10px; }
  .address { position: absolute; left: 40px; bottom: 24px; font-size: 13px; line-height: 18px; }

  /* back */
  .brand-back__ring {
    width: 110px; height: 110px; border-radius: 50%;
    border: 6px solid var(--card-white);
    margin: 44px auto 0;
  }
  .brand-back__name { font-family: "Cinzel", Georgia, serif; font-weight: 600; font-size: 42px; margin-top: 26px; letter-spacing: 1px; }
  .brand-back__site { font-family: "Cinzel", Georgia, serif; font-weight: 600; font-size: 15px; letter-spacing: 2.5px; margin-top: 14px; }
</style>
</head>
<body>
  <section class="card card--front">
    <div class="faint-mark"></div>
    <div class="holder">
      <p class="holder__name">Tom Brandish</p>
      <p class="holder__title">Regional Sales Director</p>
    </div>
    <div class="holder-rule"></div>

    <div class="brand-front">
      <span class="brand-front__dot"></span>
      <span class="brand-front__name">HARBOR LEDGER</span>
    </div>

    <div class="contacts">
      <div class="contacts__pair">
        <div class="contacts__row">
          <svg viewBox="0 0 24 24"><path d="M6.6 10.8a15.1 15.1 0 0 0 6.6 6.6l2.2-2.2a1 1 0 0 1 1-.25 11.4 11.4 0 0 0 3.6.57 1 1 0 0 1 1 1V20a1 1 0 0 1-1 1A17 17 0 0 1 3 4a1 1 0 0 1 1-1h3.5a1 1 0 0 1 1 1c0 1.25.2 2.450.57 3.57a1 1 0 0 1-.25 1z"/></svg>
          <span>410-555-0182</span>
        </div>
        <div class="contacts__row">
          <svg viewBox="0 0 24 24"><path d="M6 2h12v6H6zM3 9h18v9h-3v4H6v-4H3zm5 6v5h8v-5z"/></svg>
          <span>443-555-0164</span>
        </div>
      </div>
      <div class="contacts__row">
        <svg viewBox="0 0 24 24"><path d="M6.6 10.8a15.1 15.1 0 0 0 6.6 6.6l2.2-2.2a1 1 0 0 1 1-.25 11.4 11.4 0 0 0 3.6.57 1 1 0 0 1 1 1V20a1 1 0 0 1-1 1A17 17 0 0 1 3 4a1 1 0 0 1 1-1h3.5a1 1 0 0 1 1 1c0 1.25.2 2.450.57 3.57a1 1 0 0 1-.25 1z"/></svg>
        <span>888-555-0149 <span class="contacts__ext">Ext.318</span></span>
      </div>
      <div class="contacts__row">
        <svg viewBox="0 0 24 24"><path d="M2 5h20v14H2zm2 2v.5l8 5 8-5V7z"/></svg>
        <span>tbrandish@harborledger-example.net</span>
      </div>
      <div class="contacts__row">
        <svg viewBox="0 0 24 24"><path d="M12 2a10 10 0 1 0 0 20 10 10 0 0 0 0-20zm6.9 6h-3a15 15 0 0 0-1.3-3.9A8 8 0 0 1 18.9 8zM12 4c.8 1.2 1.5 2.5 1.9 4h-3.8c.4-1.5 1.1-2.8 1.9-4zM4.3 14a8 8 0 0 1 0-4h3.4a16 16 0 0 0 0 4zm.8 2h3a15 15 0 0 0 1.3 3.9A8 8 0 0 1 5.1 16zM8.1 8h-3a8 8 0 0 1 4.3-3.9A15 15 0 0 0 8.1 8zM12 20c-.8-1.2-1.5-2.5-1.9-4h3.8c-.4 1.5-1.1 2.8-1.9 4zm2.3-6H9.7a14 14 0 0 1 0-4h4.6a14 14 0 0 1 0 4zm.3 5.9a15 15 0 0 0 1.3-3.9h3a8 8 0 0 1-4.3 3.9zm1.7-5.9a16 16 0 0 0 0-4h3.4a8 8 0 0 1 0 4z"/></svg>
        <span>www.harborledger-example.net</span>
      </div>
    </div>

    <p class="address">718 E. Marlow St. Suite 340<br>Kellsbrook PA 21287</p>
  </section>

  <section class="card card--back">
    <div class="brand-back__ring"></div>
    <p class="brand-back__name">HARBOR LEDGER</p>
    <p class="brand-back__site">WWW.HARBORLEDGER-EXAMPLE.NET</p>
  </section>
</body>
</html>
```